Design a large parking banner – mandatory ticket validation in the shop

Banner Size:
548 cm (width) x 154 cm (height)
Note: The banner will be placed in a metal frame at our parking lot entrance, fully visible to every incoming truck driver. The message must be easy to read from a distance.
Goal of the Banner:
To inform all truck drivers that they must validate their entry ticket inside the shop, even if they are parking for a short time.
The message must be displayed in multiple languages for international drivers.
Mandatory Content:
Main message – in multiple languages (clearly separated or stacked):
Dutch (NL): Vergeet je ticket niet te valideren in de shop – verplicht, ook bij kort parkeren!
French (FR): N'oubliez pas de valider votre ticket à la boutique – obligatoire, même pour un court arrêt !
English (EN): Don't forget to validate your entry ticket in the shop – mandatory, even for short stops!
German (DE): Vergessen Sie nicht, Ihr Einfahrticket im Shop zu entwerten – Pflicht, auch bei kurzem Parken!
Polish (PL): Nie zapomnij zatwierdzić biletu w sklepie – obowiązkowe, nawet przy krótkim postoju!
Romanian (RO): Nu uitați să validați biletul în magazin – obligatoriu, chiar și pentru opriri scurte!
You can include more languages if space allows, but these are essential.
Opening Hours Block (in one section below):
Shop Opening Hours
Mon – Fri: 05:30 – 22:00
Sat & Sun: 08:00 – 22:00
Style & Branding:
The design must match the visual identity of Haulport 41Ter
Please refer to the attached photos of existing parking signage for guidance on colors, typography, and layout style
Our logo (attached) must be clearly visible and professionally integrated
Feel free to use icons or pictograms to visually support the message (e.g., ticket, truck, arrow)
Readability is key – large, bold text and high contrast colors that are visible from a distance
Target Audience:
International truck drivers – people who need fast, clear communication. Not everyone speaks the local language, so visual clarity and multilingual messaging are critical.
File Requirements:
Print-ready file (PDF or EPS) – 300 dpi at 1:10 scale
Include 5 cm bleed on all sides
Provide open source files if possible (AI or PSD)

```html
<!DOCTYPE html>
<html lang="en">
<head>
<meta charset="utf-8">
<title>Haulport 41Ter – Ticket Validation Banner</title>
<link href="https://fonts.googleapis.com/css2?family=Oswald:wght@500;600;700&family=Exo+2:ital,wght@1,500;1,600&family=Lexend:wght@500&display=swap" rel="stylesheet">
<style>
  :root {
    --page: #e6e8ec;
    --navy: #1e2363;
    --navy-light: #2b3283;
    --white: #f3f3f5;
    --yellow: #f2b420;
    --red: #d9232b;
    --tag-blue: #2f80d1;
    --green: #1f9a3c;
  }
  * { margin: 0; padding: 0; box-sizing: border-box; }
  html, body {
    width: 1200px; height: 615px; overflow: hidden;
    background: var(--page);
  }
  .banner {
    position: absolute; left: 0; top: 133px;
    width: 1200px; height: 348px; overflow: hidden;
    background: radial-gradient(ellipse at 45% 30%, var(--navy-light), var(--navy) 70%);
    color: var(--white);
  }
  .message { position: absolute; display: flex; gap: 10px; }
  .lang-tag {
    flex: none;
    width: 22px; height: 22px; margin-top: 5px;
    background: var(--tag-blue); color: var(--white);
    font: 600 13px/22px "Oswald", sans-serif; text-align: center;
    border-radius: 2px;
  }
  .message p { white-space: nowrap; }
  .accent { color: var(--yellow); }

  .msg-en { left: 17px; top: 20px; }
  .msg-en p { font: 600 25px/30.5px "Oswald", sans-serif; }
  .msg-fr { left: 423px; top: 20px; }
  .msg-fr p { font: 500 25px/29px "Oswald", sans-serif; font-style: italic; }
  .msg-de { left: 850px; top: 20px; }
  .msg-de p { font: 500 22px/23.5px "Lexend", sans-serif; }
  .msg-nl { left: 17px; top: 130px; }
  .msg-nl p { font: 500 22px/24.5px "Exo 2", sans-serif; font-style: italic; }
  .msg-pl { left: 423px; top: 128px; }
  .msg-pl p { font: 600 27px/30.5px "Oswald", sans-serif; }
  .msg-ro { left: 850px; top: 128px; }
  .msg-ro p { font: 600 22px/28px "Exo 2", sans-serif; font-style: italic; }

  .rule { position: absolute; left: 22px; top: 241px; width: 901px; height: 3px; background: var(--red); }

  .steps { position: absolute; left: 30px; top: 266px; }

  .hours-title {
    position: absolute; left: 471px; top: 266px; width: 100px;
    font: 700 27px/31px "Oswald", sans-serif; white-space: nowrap;
  }
  .hours-title span { display: block; }
  .hours-title span:last-child { letter-spacing: 6.5px; }
  .hours-divider { position: absolute; left: 585px; top: 270px; width: 3px; height: 60px; background: var(--red); }
  .hours-list {
    position: absolute; left: 599px; top: 262px;
    font: 600 32px/33px "Oswald", sans-serif; white-space: nowrap;
  }

  .brand {
    position: absolute; left: 952px; top: 276px; width: 232px;
    display: flex; align-items: center; gap: 8px;
  }
  .brand-mark { flex: none; width: 14px; height: 14px; background: var(--tag-blue); }
  .brand-name { font: 700 31px/1 "Oswald", sans-serif; color: var(--white); white-space: nowrap; }
  .brand-rule { position: absolute; left: 952px; top: 325px; width: 138px; height: 4px; background: var(--red); }
</style>
</head>
<body>
<main class="banner">
  <div class="message msg-en"><span class="lang-tag">EN</span>
    <p>Don't forget to validate your<br>entry ticket in the shop -<br><span class="accent">mandatory, even for short stops!</span></p></div>
  <div class="message msg-fr"><span class="lang-tag">FR</span>
    <p>N'oubliez pas de valider votre<br>ticket à la boutique – <span class="accent">obligatoire,</span><br><span class="accent">même pour un court arrêt !</span></p></div>
  <div class="message msg-de"><span class="lang-tag">DE</span>
    <p>Vergessen Sie nicht, Ihr<br>Einfahrticket im Shop zu<br>entwerten – <span class="accent">Pflicht, auch</span><br><span class="accent">bei kurzem Parken!</span></p></div>
  <div class="message msg-nl"><span class="lang-tag">NL</span>
    <p>Vergeet je ticket niet te<br>valideren in de shop –<br><span class="accent">verplicht, ook bij kort parkeren!</span></p></div>
  <div class="message msg-pl"><span class="lang-tag">PL</span>
    <p>Nie zapomnij zatwierdzić biletu<br>w sklepie – <span class="accent">obowiązkowe, nawet</span><br><span class="accent">przy krótkim postoju!</span></p></div>
  <div class="message msg-ro"><span class="lang-tag">RO</span>
    <p>Nu uitați să validați biletul în<br>magazin – <span class="accent">obligatoriu, chiar</span><br><span class="accent">și pentru opriri scurte!</span></p></div>

  <div class="rule"></div>

  <svg class="steps" width="430" height="66" viewBox="0 0 430 66" aria-label="Truck, then ticket, then shop">
    <g class="icon-truck" fill="var(--green)">
      <rect x="2" y="4" width="52" height="40"/>
      <path d="M58 16 h20 l12 14 v20 h-32 z"/>
      <rect x="66" y="20" width="10" height="10" fill="var(--navy)"/>
      <rect x="2" y="48" width="56" height="4"/>
      <circle cx="18" cy="52" r="8"/><circle cx="70" cy="52" r="8"/>
    </g>
    <g class="icon-arrow" fill="none" stroke="var(--white)" stroke-width="6" stroke-linecap="round" stroke-linejoin="round">
      <path d="M114 32 h36 M138 18 l14 14 -14 14"/>
      <path d="M286 32 h36 M310 18 l14 14 -14 14"/>
    </g>
    <g class="icon-ticket">
      <path d="M186 4 h74 a6 6 0 0 0 6 6 v44 a6 6 0 0 0 -6 6 h-74 a6 6 0 0 0 -6 -6 v-44 a6 6 0 0 0 6 -6 z" fill="var(--white)"/>
      <rect x="188" y="12" width="70" height="40" rx="4" fill="none" stroke="var(--navy)" stroke-width="2"/>
      <text x="223" y="40" text-anchor="middle" font-family="Oswald, sans-serif" font-weight="700" font-size="20" fill="var(--navy)">TICKET</text>
    </g>
    <g class="icon-shop" fill="var(--yellow)">
      <rect x="348" y="0" width="68" height="13"/>
      <text x="382" y="11" text-anchor="middle" font-family="Oswald, sans-serif" font-weight="600" font-size="11" fill="var(--navy)">SHOP</text>
      <path d="M348 17 h68 v40 h-10 v-22 h-16 v22 h-42 z"/>
      <rect x="360" y="32" width="10" height="8" fill="var(--navy)"/>
    </g>
  </svg>

  <div class="hours-title"><span>OPENING</span><span>HOURS</span></div>
  <div class="hours-divider"></div>
  <div class="hours-list">Mon - Fri: 05:30 - 22:00<br>Sat &amp; Sun: 08:00 - 22:00</div>

  <div class="brand"><span class="brand-mark"></span><span class="brand-name">Haulport 41Ter</span></div>
  <div class="brand-rule"></div>
</main>
</body>
</html>
```